Stylish Business Cards Wanted

- DOUBLE SIDED Design Required -

High end, edgy cards for a corporate and personal stylist. Must include logo,
Name: Belinda Harwick
Title: Director and Stylist
telephone : +61 8 7142 5809
email: belinda@theloombriefing.example
website: theloombriefing.example
Tag: Corporate Workwear & Uniform Specialist | Personal Stylist
Would like nice icons for telephone, email, website

Target Market(s)

Businesses wanting stylish uniforms, people wanting stylish wardrobes

Industry/Entity Type

Corporate Workwear Stylist

Contact Information for Business Card

I would like black, white and gold foiling incorporated in the design - possibly a touch of the other colours on my branding guide attached Name: Belinda Harwick Title: Director and Stylist telephone : +61 8 7142 5809 email: belinda@theloombriefing.example website: theloombriefing.example Tag: Corporate Workwear & Uniform Specialist | Personal Stylist Would like nice icons for telephone, email, website

Font styles to use
Other font styles liked:
• Raleway

Colors

Designer to choose colors to be used in the design.

Requirements
Must have
• Gold foil accents

```html
<!DOCTYPE html>
<html lang="en">
<head>
<meta charset="utf-8">
<title>The Loom Briefing — Business Cards</title>
<link rel="stylesheet" href="https://fonts.googleapis.com/css2?family=Montserrat:wght@400;600;700&family=Raleway:wght@400;500&display=swap">
<style>
  :root {
    --backdrop: #c4c4c4;
    --card: #232323;
    --gold: #e2b54a;
    --white: #ffffff;
    --soft-white: #f2f2f2;
  }
  * { box-sizing: border-box; margin: 0; padding: 0; }
  html, body { width: 1200px; height: 788px; overflow: hidden; }
  body {
    background: var(--backdrop);
    font-family: "Montserrat", Arial, sans-serif;
    position: relative;
  }
  .card {
    position: absolute;
    background: var(--card);
    border: 2px solid var(--gold);
    box-shadow: 0 14px 30px rgba(0,0,0,.28);
    color: var(--white);
  }
  .brand-name {
    font-family: "Montserrat", Arial, sans-serif;
    font-weight: 600;
    color: var(--white);
    text-transform: uppercase;
    letter-spacing: .16em;
    text-align: center;
    line-height: 1.25;
  }
  .brand-mark {
    display: block;
    width: 12px; height: 12px;
    background: var(--gold);
    margin: 0 auto 14px;
  }

  /* Front: portrait contact side */
  .card-front {
    left: 90px; top: 120px;
    width: 310px; height: 542px;
    display: flex; flex-direction: column; align-items: center;
    padding: 84px 26px 0;
  }
  .card-front .brand-name { font-size: 26px; }
  .person { margin-top: 92px; text-align: center; }
  .person-name {
    font-weight: 700; font-size: 22px; letter-spacing: .04em;
    color: var(--gold); text-transform: uppercase;
  }
  .person-title {
    font-family: "Raleway", Arial, sans-serif;
    font-size: 14px; margin-top: 6px; color: var(--soft-white);
  }
  .icon-row {
    display: flex; align-items: center; gap: 8px;
    margin-top: 34px; width: 100%;
  }
  .rule { flex: 1; height: 1px; background: var(--gold); }
  .icon {
    width: 30px; height: 30px; border-radius: 50%;
    background: var(--gold);
    display: flex; align-items: center; justify-content: center;
  }
  .icon svg { width: 16px; height: 16px; }
  .contact-list {
    list-style: none; margin-top: 24px; text-align: center;
    font-family: "Raleway", Arial, sans-serif;
    font-size: 14px; line-height: 1.75; color: var(--soft-white);
  }

  /* Back: landscape brand side */
  .card-back {
    left: 450px; top: 210px;
    width: 680px; height: 390px;
    display: flex; flex-direction: column; align-items: center;
    padding-top: 108px;
  }
  .card-back .brand-name { font-size: 36px; }
  .tagline {
    position: absolute; left: 0; right: 0; bottom: 44px;
    text-align: center;
    font-family: "Raleway", Arial, sans-serif;
    font-weight: 500; font-size: 17px; color: var(--gold);
    letter-spacing: .02em;
  }
</style>
</head>
<body>

<section class="card card-front" aria-label="Business card, contact side">
  <div class="brand">
    <span class="brand-mark" aria-hidden="true"></span>
    <p class="brand-name">The Loom<br>Briefing</p>
  </div>

  <div class="person">
    <h1 class="person-name">Belinda Harwick</h1>
    <p class="person-title">Director and Stylist</p>
  </div>

  <div class="icon-row">
    <span class="rule"></span>
    <span class="icon" aria-label="Telephone">
      <svg viewBox="0 0 24 24"><path fill="#232323" d="M6.6 10.8a15.1 15.1 0 0 0 6.6 6.6l2.2-2.2c.3-.3.7-.4 1-.2 1.1.4 2.3.6 3.6.6.6 0 1 .4 1 1V20c0 .6-.4 1-1 1A17 17 0 0 1 3 4c0-.6.4-1 1-1h3.5c.6 0 1 .4 1 1 0 1.3.2 2.5.6 3.6.1.3 0 .7-.2 1z"/></svg>
    </span>
    <span class="icon" aria-label="Email">
      <svg viewBox="0 0 24 24"><rect x="3" y="6" width="18" height="12" fill="#232323"/><path d="M3 6l9 7 9-7" fill="none" stroke="#e2b54a" stroke-width="1.6"/></svg>
    </span>
    <span class="icon" aria-label="Website">
      <svg viewBox="0 0 24 24" fill="none" stroke="#232323" stroke-width="1.8"><circle cx="12" cy="12" r="9"/><ellipse cx="12" cy="12" rx="4" ry="9"/><path d="M3 12h18"/></svg>
    </span>
    <span class="rule"></span>
  </div>

  <ul class="contact-list">
    <li>+61 8 7142 5809</li>
    <li>belinda@theloombriefing.example</li>
    <li>www.theloombriefing.example</li>
  </ul>
</section>

<section class="card card-back" aria-label="Business card, brand side">
  <div class="brand">
    <span class="brand-mark" aria-hidden="true"></span>
    <p class="brand-name">The Loom<br>Briefing</p>
  </div>
  <p class="tagline">Corporate Workwear &amp; Uniform Specialist | Personal Stylist</p>
</section>

</body>
</html>
```